A new fresh and flat K&T Logistics Brochure Design A4 - 4 pages

Our client is an established International Logistics firm looking to upgrade their sales brochure.
We would like the designer to create concepts that are flat, modern and communicate reliability and expediency to our clients. We want the brochure to maintain a degree of white space and minimal design.
Introduction
LOGISTICS - it's what we do best! We're proud to say so after 27 years (and counting) of organic growth within the 3PL industry. Starting off in Meridian, Mississippi with a fleet of 4 trucks in 1987, K&T is today a global 3PL company with offices in the United States and Asia Pacific region.
Our goal has always been to serve our clients by getting things done, and getting them done right.
Format: A4 4-sided brochure
Pg 1 Front Page - Company name and logo, and vector design concept to make front page unique. Please try to include some kind of container reference design on the front page (e.g 2D or 3D vector, transparent overlay etc...), place this design element somewhere in the middle or bttom of the page.
Pg 2 and/or Pg 3
- Introduction and Core services Including: ABOUT, SERVICES, CONTRACT LOGISTICS, K&T INTEL (following the menu content of our website www.ktvfr.example)
- Text space to explain Services in more detail.
Social proof (existing client testimonials/feedback.)
- A 'C.A.R.E' acronym design element, including the words: Communicative, Accessible, Responsible, Efficient
Pg 4 Back Page- Contact information, Call to action.
Throughut the brochure please leave space for images as you deem appropriate and we will update late OR even better usesome of your own stock images.
Color theme: Based on corporate colors (but not limited to), see website
http://www.ktvfr.example
Try diffent font types to the website both serif and sans serif
Include several CTAs throughout the brochure.
You can use both the attached pdf brochure and the website for content.
We would also appreciate if you could also enhance the logo to make it 'pop' (keep shape and style).

```html
<!DOCTYPE html>
<html lang="en">
<head>
<meta charset="utf-8">
<title>K&amp;T Logistics – Contact</title>
<link rel="stylesheet" href="https://fonts.googleapis.com/css2?family=Barlow+Condensed:wght@500;600&family=Arimo:wght@400&display=swap">
<style>
  :root {
    --page: #ffffff;
    --frame: #9a9a9a;
    --steel: #7590a8;
    --steel-light: #dfe4ea;
    --orange: #f7941d;
    --ink: #1a1a1a;
    --white: #ffffff;
    --logo: #6d8299;
    --tagline: #5f7488;
  }
  * { margin: 0; padding: 0; box-sizing: border-box; }
  html, body { width: 1200px; height: 849px; overflow: hidden; background: var(--page); }
  .page {
    position: relative;
    width: 1200px; height: 849px;
    border: 1px solid var(--frame);
    background: var(--page);
    font-family: "Arimo", Arial, sans-serif;
  }
  .shapes { position: absolute; left: 0; top: 0; }

  .brand {
    position: absolute; left: 790px; top: 100px;
    display: flex; align-items: center; gap: 8px;
  }
  .brand-mark { width: 14px; height: 14px; background: var(--logo); }
  .brand-name {
    font-family: "Barlow Condensed", "Arial Narrow", sans-serif;
    font-weight: 600; font-size: 30px; line-height: 1;
    color: var(--logo);
  }
  .brand-tagline {
    font-size: 11px; color: var(--tagline); margin-top: 12px;
  }

  .contact-title {
    position: absolute; left: 97px; top: 330px;
    font-family: "Barlow Condensed", "Arial Narrow", sans-serif;
    font-weight: 600; font-size: 33px; line-height: 1;
    color: var(--orange);
  }
  .office { position: absolute; width: 190px; }
  .office-region {
    font-family: "Barlow Condensed", "Arial Narrow", sans-serif;
    font-weight: 600; font-size: 12px; line-height: 13px;
    color: var(--ink);
  }
  .office-details {
    font-size: 9.5px; line-height: 12px; color: var(--white);
  }
  .office--china { left: 97px; top: 381px; }
  .office--usa { left: 97px; top: 459px; }
  .office--hk { left: 300px; top: 381px; }
  .contact-email {
    position: absolute; left: 300px; top: 461px;
    font-family: "Barlow Condensed", "Arial Narrow", sans-serif;
    font-weight: 500; font-size: 11.5px; color: var(--white);
  }
  .website {
    position: absolute; left: 860px; top: 792px;
    font-family: "Barlow Condensed", "Arial Narrow", sans-serif;
    font-weight: 600; font-size: 15px; color: var(--orange);
  }
</style>
</head>
<body>
<main class="page">
  <svg class="shapes" width="1200" height="849" viewBox="0 0 1200 849" aria-hidden="false">
    <defs>
      <linearGradient id="dockTones" x1="0" y1="0" x2="1" y2="1">
        <stop offset="0" stop-color="#5a7fb8"/>
        <stop offset="0.45" stop-color="#c9d3dc"/>
        <stop offset="0.75" stop-color="#d9c06a"/>
        <stop offset="1" stop-color="#7c8a96"/>
      </linearGradient>
    </defs>
    <polygon class="band band--top" points="120,262 855,262 838,296 102,296" fill="var(--steel-light)"/>
    <polygon class="band band--bottom" points="348,566 1080,566 1062,600 330,600" fill="var(--steel-light)"/>
    <polygon class="contact-panel" points="0,303 682,303 540,557 0,557" fill="var(--steel)"/>
    <polygon class="dock-photo" points="690,303 1185,303 1050,557 548,557"
             fill="url(#dockTones)" role="img"
             aria-label="Warehouse loading docks with a forklift and container trucks"/>
  </svg>

  <div class="brand">
    <span class="brand-mark"></span>
    <span class="brand-name">K&amp;T</span>
    <span class="brand-tagline">Logistics and Supply Chain Solutions</span>
  </div>

  <h1 class="contact-title">Contact US</h1>

  <section class="office office--china">
    <h2 class="office-region">China</h2>
    <p class="office-details">K&amp;T Logistics<br>12F, Harbour Point Tower, Binhai Road,<br>Nanshan District, Shenzhen 518000,<br>Telephone: +86 755 0000 0142</p>
  </section>

  <section class="office office--usa">
    <h2 class="office-region">USA</h2>
    <p class="office-details">K&amp;T Transport<br>1200 Riverbend Parkway<br>Meridian, MS 39300 USA<br>Telephone: +1 601 555 0138</p>
  </section>

  <section class="office office--hk">
    <h2 class="office-region">Hong Kong</h2>
    <p class="office-details">K&amp;T Logistics<br>8F Lotus Trade Centre<br>42 Harbour Street, Central,<br>Telephone: +852 0000 4127</p>
  </section>

  <p class="contact-email">Email: info@ktfreight.example</p>

  <p class="website">www.ktvfr.example</p>
</main>
</body>
</html>
```